Boutique town planning business needs a Business Card design

We need a business card design for a new company called The Zoning Bridgeway. We provide town planning and urban design services to government, business and community groups. We would like to see the designs use the colours in the logo (blue, deep red, green and amber), plenty of white and including black and grey in the writing. The final design should communicate collaboration, creativity and professionalism and that we are approachable.

Industry/Entity Type

Town

```html
<!DOCTYPE html>
<html lang="en">
<head>
<meta charset="utf-8">
<title>The Zoning Bridgeway – Business Card</title>
<link rel="stylesheet" href="https://fonts.googleapis.com/css2?family=Exo+2:wght@400;500;600&display=swap">
<style>
  :root {
    --backdrop: #c9ccd0;
    --card: #ffffff;
    --ink: #2b2b2b;
    --ink-soft: #555555;
    --green: #2e9e2e;
    --black: #0d0d0d;
    --on-dark: #f2f2f2;
    --mark: #3a9ec2;
  }
  * { box-sizing: border-box; margin: 0; padding: 0; }
  html, body { width: 1200px; height: 864px; overflow: hidden; }
  body {
    background: var(--backdrop);
    font-family: "Exo 2", sans-serif;
    color: var(--ink);
    position: relative;
  }
  .card {
    position: absolute;
    top: 278px;
    width: 540px;
    height: 309px;
    background: var(--card);
    box-shadow: 0 6px 18px rgba(0,0,0,0.18);
    overflow: hidden;
  }
  .card--front { left: 45px; }
  .card--back { left: 615px; }

  .brand {
    display: flex;
    align-items: center;
    gap: 12px;
  }
  .brand__dot {
    width: 34px; height: 34px;
    border-radius: 50%;
    background: var(--mark);
    flex: none;
  }
  .brand__name {
    font-weight: 600;
    font-size: 24px;
    color: var(--ink);
    letter-spacing: 0.2px;
    white-space: nowrap;
  }
  .card--front .brand {
    position: absolute;
    left: 50%; top: 50%;
    transform: translate(-50%, -50%);
  }
  .card--front .brand__dot { width: 46px; height: 46px; }
  .card--front .brand__name { font-size: 30px; }

  .wave { position: absolute; inset: 0; }
  .card--back .brand {
    position: absolute;
    left: 34px; top: 118px;
  }
  .card--back .brand__dot { width: 26px; height: 26px; }
  .card--back .brand__name { font-size: 19px; }

  .person {
    position: absolute;
    left: 40px; top: 178px;
  }
  .person__name {
    font-size: 19px;
    font-weight: 500;
    color: var(--green);
    letter-spacing: 1px;
  }
  .person__title {
    font-size: 12px;
    color: var(--ink-soft);
    margin-top: 2px;
    margin-left: 14px;
  }

  .contact {
    position: absolute;
    right: 18px; top: 40px;
    list-style: none;
    color: var(--on-dark);
    font-size: 10px;
    line-height: 1.35;
    text-align: right;
  }
  .contact__item {
    display: flex;
    justify-content: flex-end;
    align-items: center;
    gap: 6px;
    margin-bottom: 9px;
  }
  .contact__icon { width: 10px; height: 10px; flex: none; fill: var(--on-dark); }
</style>
</head>
<body>

<section class="card card--front" aria-label="Card front">
  <div class="brand">
    <span class="brand__dot"></span>
    <span class="brand__name">The Zoning Bridgeway</span>
  </div>
</section>

<section class="card card--back" aria-label="Card back">
  <svg class="wave" viewBox="0 0 540 309" aria-hidden="true">
    <path fill="var(--green)" d="M452,0 C378,40 398,172 326,232 C258,290 120,266 0,262 L0,309 L540,309 L540,0 Z"/>
    <path fill="var(--black)" d="M482,0 C408,46 432,182 356,246 C290,300 150,286 0,281 L0,309 L540,309 L540,0 Z"/>
  </svg>

  <div class="brand">
    <span class="brand__dot"></span>
    <span class="brand__name">The Zoning Bridgeway</span>
  </div>

  <div class="person">
    <div class="person__name">MARTIN HALE</div>
    <div class="person__title">Managing Director</div>
  </div>

  <ul class="contact">
    <li class="contact__item"><span>41 Fern St, Level 6<br>Northgate NTG</span>
      <svg class="contact__icon" viewBox="0 0 10 10"><path d="M5 0a3.5 3.5 0 0 0-3.5 3.5C1.5 6 5 10 5 10s3.5-4 3.5-6.5A3.5 3.5 0 0 0 5 0zm0 5a1.5 1.5 0 1 1 0-3 1.5 1.5 0 0 1 0 3z"/></svg></li>
    <li class="contact__item"><span>014 552 7310</span>
      <svg class="contact__icon" viewBox="0 0 10 10"><path d="M2 0l2 2.5-1.2 1.2a6 6 0 0 0 3.5 3.5L7.5 6 10 8 8.5 10C4 10 0 6 0 1.5z"/></svg></li>
    <li class="contact__item"><span>014 552 7311</span>
      <svg class="contact__icon" viewBox="0 0 10 10"><path d="M2.5 0h5v10h-5zM3.5 1v7h3V1z"/></svg></li>
    <li class="contact__item"><span>mhale@zbmail.com</span>
      <svg class="contact__icon" viewBox="0 0 10 10"><path d="M0 2h10v6H0zm1 1v.3l4 2.5 4-2.5V3z"/></svg></li>
    <li class="contact__item"><span>www.zoningbridgeway.com</span>
      <svg class="contact__icon" viewBox="0 0 10 10"><path d="M5 0a5 5 0 1 0 0 10A5 5 0 0 0 5 0zm0 1c.7.8 1.1 2 1.2 3.5H3.8C3.9 3 4.3 1.8 5 1zM1 5.5h1.8c.1 1.3.4 2.4.9 3.2A4 4 0 0 1 1 5.5zm2.8 0h2.4C6.1 7 5.7 8.2 5 9c-.7-.8-1.1-2-1.2-3.5zm3.4 0H9a4 4 0 0 1-2.7 3.2c.5-.8.8-1.9.9-3.2zM1 4.5a4 4 0 0 1 2.7-3.2c-.5.8-.8 1.9-.9 3.2zm6.2 0c-.1-1.3-.4-2.4-.9-3.2A4 4 0 0 1 9 4.5z"/></svg></li>
  </ul>
</section>

</body>
</html>
```